Etiketten-Design für Dankeswein
Zielgruppe
Kelvora:
Wir stellen für unsere Kunden einen Dankeswein her. Er soll eine Hommage an die Freundschaft und Partnerschaft sein.
Subtitle, could be, but perhaps not:
When we meet, anything can happen.
Name: Kelvora (evtl. Änderung auf Tarnis)
Aufgabenstellung
Das Ettikett darf auch bunt sein, aber es sollte vorallem sehr Professionell sein.
Der Wein wird rötlich sein, die Flasche weiss durchsichtig. Es werden wahrscheinlich 0,5l Flaschen.
Die Form des Ettikets, kann noch definiert werden.
Es geht um eine Homage an das Treffen von Menschen und die Freundschaft.
Kelvora
Hintergrundinfos, die eher für den Hintergrund, Einarbeitung und kleine Abbildung gedacht sind.
PLORAX: ist eine IT Firma, die von 2 Partnern gegründet wurde. Das Logo sollte mit drauf, evtl. kann man auch sich an diesen Farben orientieren.
Familie Dormak: Die Tiersymbole repräsentieren die beiden Eltern. Das geschwungene H ist das Familienzeichen. Wenn man es rotiert. ähnelt es wieder einem Schmetterling. Vielleicht kann man da grafisch etwas machen?
Das geschwungene H oder die Tiersymbole haben hohen emotionalen Wert. In dem Wappen ist das neue Familiensymbol eingearbeitet in das noch ältere Familienwappen der Familie. Prio hat das geschwungene H
Für das Ettikett gibt es leider rechtliche Pflichtangaben:
PLORAX GmbH
Lindauring 14 CH-4057 Basel
Erzeugerab füllung:D- RP 7 348 962
A.P.-Nr.7 348 962 XXXX
11,0%vol 50 cl Enthält Sulfite
Deutscher Qualitätswein – Mosel
kelvora-beispiel.eu

```html
<!DOCTYPE html>
<html lang="de">
<head>
<meta charset="utf-8">
<title>Tarnis – Dankeswein Etikett</title>
<link rel="stylesheet" href="https://fonts.googleapis.com/css2?family=Barlow+Semi+Condensed:wght@500;600&family=Montserrat:wght@500;600&display=swap">
<style>
  :root {
    --page: #ecebe8;
    --label: #0b0b0c;
    --ornament: #2a2a2c;
    --blue: #3b8fcb;
    --green: #7cb93b;
    --grey: #a9abae;
    --teal: #35a9c9;
    --white: #ffffff;
  }
  * { margin: 0; padding: 0; box-sizing: border-box; }
  html, body {
    width: 1200px;
    height: 2748px;
    overflow: hidden;
    background: var(--page);
  }
  .canvas {
    position: relative;
    width: 1200px;
    height: 2748px;
  }
  .label {
    position: absolute;
    left: 120px;
    top: 754px;
    width: 960px;
    height: 1240px;
    background: var(--label);
    border-radius: 56px;
    overflow: hidden;
  }
  .family-sign {
    position: absolute;
    left: 20px;
    top: 40px;
    width: 470px;
    height: 330px;
    border-radius: 50% 40% 55% 45%;
    background: radial-gradient(ellipse at 40% 50%, var(--ornament) 0%, rgba(42,42,44,0.35) 55%, rgba(11,11,12,0) 75%);
  }
  .butterfly {
    position: absolute;
    left: 386px;
    top: 232px;
    width: 499px;
    height: 361px;
    border-radius: 46% 46% 40% 40%;
    background: linear-gradient(135deg, #7cc04a 0%, #4fb0a0 45%, #3b8fcb 100%);
    opacity: 0.85;
  }
  .title {
    position: absolute;
    left: 106px;
    top: 614px;
    width: 424px;
    display: flex;
    flex-direction: column;
    gap: 17px;
  }
  .title-word {
    height: 136px;
    display: flex;
    align-items: center;
    padding-left: 22px;
    font-family: "Barlow Semi Condensed", "Arial Narrow", sans-serif;
    font-weight: 600;
    font-size: 104px;
    letter-spacing: 14px;
    line-height: 1;
    color: var(--white);
  }
  .title-word--blue { background: var(--blue); }
  .title-word--green { background: var(--green); }
  .title-word--grey { background: var(--grey); }
  .dog {
    position: absolute;
    left: 635px;
    top: 582px;
    width: 280px;
    height: 216px;
    border-radius: 30% 60% 45% 40%;
    background: linear-gradient(120deg, #3b8fcb 0%, var(--teal) 100%);
    opacity: 0.8;
  }
  .thanks {
    position: absolute;
    left: 698px;
    top: 1042px;
    height: 36px;
    font-family: "Montserrat", Arial, sans-serif;
    font-weight: 500;
    font-size: 34px;
    line-height: 36px;
    letter-spacing: 6px;
    color: var(--teal);
    transform: rotate(-49deg);
    transform-origin: left bottom;
    white-space: nowrap;
  }
  .company {
    position: absolute;
    left: 150px;
    top: 1088px;
    display: flex;
    align-items: center;
    gap: 12px;
    font-family: "Montserrat", Arial, sans-serif;
    font-weight: 600;
    font-size: 42px;
    letter-spacing: 3px;
    color: var(--white);
  }
  .company-mark {
    width: 14px;
    height: 14px;
    background: var(--white);
  }
</style>
</head>
<body>
  <main class="canvas">
    <section class="label">
      <div class="family-sign" role="img" aria-label="Geschwungenes H, das Familienzeichen, als dezentes Hintergrundornament"></div>
      <div class="butterfly" role="img" aria-label="Schmetterling in Grün- und Blautönen"></div>
      <h1 class="title">
        <span class="title-word title-word--blue">HERE</span>
        <span class="title-word title-word--green">WE</span>
        <span class="title-word title-word--grey">ARE</span>
      </h1>
      <div class="dog" role="img" aria-label="Tiersymbol: Hundekopf in Blautönen"></div>
      <p class="thanks">THANK YOU</p>
      <div class="company"><span>PLORAX</span><span class="company-mark"></span></div>
    </section>
  </main>
</body>
</html>
```